CalmPeak Nurses' Manifesto

Design a manifesto to inspire and motivate nurses to work at minimum standards of excellence in their nursing practice.

The manifesto will become a feature of our website, at conferences, workshops and retreats. It will also be featured on other marketing tools.

Primary Market:
Nurses and/or other healthcare professionals (specifically Doctors, Occupational Therapists, Psychologists and Social Workers).

However the manifesto is equally applicable to all nurses and healthcare professionals from new graduates to very experienced senior clinicians, administration officers,managers and healthcare executive personnel.

Mainly females and primarily 35 to 65 years old, which suggests people in this target age group have extensive experience, but have become jaded'.

The purpose of our business is to assist healthcare professionals, primarily nurses, to maintain their enthusiasm and excellence in service provision, for their benefit as well as the benefit of the clients.

I have attached:
File 1: Copy Samples and examples: which has the copy for the manifesto, examples that appeal to us and our 3 attempts.
File 2: Our colour Spec Sheet, HOWEVER the colours are not necessary limited to these colours. These colours are not in the logo that will be on the manifesto. The colours on the logo attached can/or also be used.
File 3: Prototype logo. The final logo will be available within 3 to 4 days.

Industry/Entity Type

Healthcare

Requirements
Must have
• Must use the copy as per the attached file.

It should be contemporary, eye catching and motivational.

Should not have
• MUST BE EASY TO READ. Each line MUST be clearly defined from each other.

```html
<!DOCTYPE html>
<html lang="en">
<head>
<meta charset="utf-8">
<title>CalmPeak Nurses' Manifesto</title>
<link rel="stylesheet" href="https://fonts.googleapis.com/css2?family=PT+Sans:wght@400;700&display=swap">
<style>
:root{
  --sky:#3d8fe0;
  --navy:#1e4fa8;
  --deep-navy:#1a3692;
  --brown:#8b5a1a;
  --ink:#111111;
  --magenta:#e61fbf;
  --lime:#8cc63f;
  --pale-blue:#8ec5ec;
  --green:#2f9a2a;
  --blue:#2a78d6;
  --red:#e2161d;
  --orange:#f2592a;
  --leaf:#5db52f;
  --purple:#7a3fd6;
  --steel:#2c6db8;
  --partner-green:#3f8a2e;
  --logo-slate:#6a7480;
  --paper:#ffffff;
}
*{margin:0;padding:0;box-sizing:border-box}
html,body{width:900px;height:1200px;overflow:hidden;background:var(--paper)}
.manifesto{position:relative;width:900px;height:1200px;font-family:"PT Sans",sans-serif;background:var(--paper);overflow:hidden}
.ln{position:absolute;line-height:1;white-space:nowrap}
.j{white-space:normal;text-align:justify;text-align-last:justify}
.band{position:absolute;background:var(--sky)}
.title{left:50px;top:38px;font-size:62px;color:var(--sky)}
.deliver{color:var(--navy)}
.always-lead{color:var(--brown)}
.self-care{color:var(--ink)}
.learner{color:var(--magenta)}
.respect{color:var(--ink)}
.smile{color:var(--deep-navy)}
.seek{color:var(--lime)}
.adopt{color:var(--pale-blue)}
.adopt-word{position:absolute;left:30px;top:795px;font-size:34px;line-height:1;color:var(--pale-blue);transform:rotate(-90deg);transform-origin:left top}
.trust{color:var(--green)}
.respond{color:var(--blue)}
.support{color:var(--red)}
.learn{color:var(--magenta)}
.choose{color:var(--ink)}
.celebrate{color:var(--orange)}
.unique{color:var(--leaf)}
.right-thing{color:var(--ink)}
.follow{color:var(--red)}
.solution{color:var(--purple)}
.lead{color:var(--sky)}
.delight{color:var(--steel)}
.nurse{color:var(--brown)}
.brand-mark{position:absolute;left:612px;top:995px;width:84px;height:84px;border-radius:50%;background:var(--logo-slate);opacity:.25}
.brand-name{position:absolute;left:640px;top:1050px;font-size:30px;line-height:1.05;color:var(--logo-slate)}
.partner-square{position:absolute;left:62px;top:1140px;width:40px;height:40px;background:var(--partner-green)}
.partner-name{position:absolute;left:118px;top:1146px;font-size:22px;line-height:1;color:var(--partner-green)}
.tagline{position:absolute;left:490px;top:1130px;width:390px;height:62px;background:var(--sky);color:var(--paper);font-size:32px;line-height:62px;padding-left:22px}
.tagline b{font-size:42px;font-weight:400}
.sp{letter-spacing:.35em}
</style>
</head>
<body>
<main class="manifesto">
  <div class="band" style="left:580px;top:0;width:300px;height:14px"></div>
  <div class="band" style="left:30px;top:0;width:16px;height:14px"></div>
  <div class="band" style="left:30px;top:1135px;width:16px;height:57px"></div>

  <h1 class="ln title" style="font-weight:400">Nurses' Manifesto</h1>
  <div class="ln deliver" style="left:603px;top:36px;font-size:28px">Deliver</div>
  <div class="ln deliver" style="left:603px;top:58px;font-size:50px">care <span style="font-size:26px">skillfully.</span></div>

  <div class="ln always-lead" style="left:38px;top:124px;font-size:48px">Always <span style="font-size:29px">lead with purpose, passion and commitment.</span></div>

  <!-- left column -->
  <div class="ln j self-care" style="left:40px;top:168px;width:348px;font-size:27px">Look after <span style="font-size:44px">yourself</span></div>
  <div class="ln j self-care" style="left:40px;top:212px;width:348px;font-size:27px">and value your <span style="font-size:42px">health</span></div>
  <div class="ln j self-care" style="left:40px;top:258px;width:348px;font-size:28px">as much as you value</div>
  <div class="ln j self-care" style="left:40px;top:292px;width:348px;font-size:28px">the health of others.</div>
  <div class="ln j learner" style="left:40px;top:326px;width:348px;font-size:28px"><span style="font-size:44px">Be</span> a lifelong learner.</div>
  <div class="ln respect" style="left:38px;top:370px;font-size:22px"><span style="font-size:54px">Respect</span> the limits of</div>
  <div class="ln j respect" style="left:38px;top:428px;width:350px;font-size:22px"><span style="font-size:28px">people</span>'s knowledge and share</div>
  <div class="ln j respect" style="left:38px;top:459px;width:350px;font-size:22px">your knowledge generously.</div>
  <div class="ln smile" style="left:38px;top:490px;font-size:32px"><span style="font-size:60px">Smile</span> and infect</div>
  <div class="ln j smile" style="left:38px;top:545px;width:350px;font-size:32px">others with your</div>
  <div class="ln j smile sp" style="left:38px;top:576px;width:350px;font-size:32px">happiness</div>
  <div class="ln seek" style="left:38px;top:612px;font-size:50px"><b>Seek</b> success</div>
  <div class="ln seek" style="left:38px;top:664px;font-size:38px">firstly from within.</div>
  <div class="adopt-word">Adopt</div>
  <div class="ln adopt" style="left:92px;top:718px;font-size:32px">a ‘can do’ attitude</div>
  <div class="ln adopt" style="left:92px;top:754px;font-size:32px">to everything that</div>
  <div class="ln adopt" style="left:92px;top:789px;font-size:32px">comes your way.</div>

  <!-- middle column -->
  <div class="ln trust" style="left:403px;top:168px;font-size:100px;letter-spacing:.04em">Trust</div>
  <div class="ln j trust" style="left:405px;top:272px;width:258px;font-size:22px">your knowledge and</div>
  <div class="ln j trust" style="left:405px;top:296px;width:258px;font-size:22px">seek advice only from</div>
  <div class="ln j trust" style="left:405px;top:320px;width:258px;font-size:22px">respected sources.</div>
  <div class="ln respond" style="left:401px;top:342px;font-size:64px">Respond</div>
  <div class="ln j respond" style="left:403px;top:423px;width:262px;font-size:24px">to complex situations</div>
  <div class="ln respond" style="left:403px;top:449px;font-size:40px;letter-spacing:.02em">innovatively,</div>
  <div class="ln j respond" style="left:403px;top:490px;width:262px;font-size:22px"><span style="font-size:40px">creatively</span> and</div>
  <div class="ln j respond" style="left:403px;top:532px;width:262px;font-size:24px"><span style="font-size:40px">safely</span> within the</div>
  <div class="ln j respond" style="left:403px;top:574px;width:262px;font-size:24px">scope of your</div>
  <div class="ln j respond sp" style="left:403px;top:604px;width:262px;font-size:24px">practice.</div>
  <div class="ln support" style="left:400px;top:642px;font-size:60px;letter-spacing:.04em">Support</div>
  <div class="ln j support" style="left:400px;top:710px;width:265px;font-size:33px">your colleagues</div>
  <div class="ln j support" style="left:400px;top:748px;width:265px;font-size:33px">and champion</div>
  <div class="ln j support" style="left:400px;top:786px;width:265px;font-size:33px">their purpose.</div>

  <!-- right column -->
  <div class="ln learn" style="left:680px;top:162px;font-size:60px">Learn</div>
  <div class="ln j learn" style="left:681px;top:222px;width:176px;font-size:22px;letter-spacing:.12em">something</div>
  <div class="ln learn" style="left:681px;top:246px;font-size:22px">new each day.</div>
  <div class="ln choose" style="left:680px;top:276px;font-size:46px">Choose</div>
  <div class="ln j choose" style="left:680px;top:320px;width:177px;font-size:26px">your thoughts</div>
  <div class="ln j choose" style="left:680px;top:347px;width:177px;font-size:26px">wisely, they</div>
  <div class="ln j choose" style="left:680px;top:373px;width:177px;font-size:26px">create your</div>
  <div class="ln choose" style="left:680px;top:402px;font-size:36px;letter-spacing:.18em">reality.</div>
  <div class="ln celebrate" style="left:680px;top:448px;font-size:32px">Celebrate,</div>
  <div class="ln j celebrate" style="left:680px;top:484px;width:177px;font-size:24px"><span style="font-size:32px">respect</span> and</div>
  <div class="ln j celebrate" style="left:680px;top:520px;width:177px;font-size:32px">v a l u e</div>
  <div class="ln j celebrate" style="left:680px;top:557px;width:177px;font-size:26px">the diversity</div>
  <div class="ln j celebrate" style="left:680px;top:585px;width:177px;font-size:26px">of Australian</div>
  <div class="ln j celebrate sp" style="left:680px;top:613px;width:177px;font-size:26px">culture.</div>
  <div class="ln j unique" style="left:680px;top:645px;width:177px;font-size:26px"><span style="font-size:52px">You</span> are</div>
  <div class="ln unique" style="left:680px;top:700px;font-size:42px">unique,</div>
  <div class="ln j unique" style="left:680px;top:757px;width:177px;font-size:27px">revel in your</div>
  <div class="ln unique" style="left:680px;top:789px;font-size:27px">individuality.</div>

  <!-- closing lines -->
  <div class="ln right-thing" style="left:38px;top:832px;font-size:30px"><span style="font-size:38px">Always</span> do the right thing without exception.</div>
  <div class="ln solution" style="left:710px;top:826px;font-size:46px">Always</div>
  <div class="ln follow" style="left:38px;top:874px;font-size:26px">Only <span style="font-size:38px">follow</span> exceptional leaders.</div>
  <div class="ln solution" style="left:533px;top:876px;font-size:32px">be solution focused.</div>
  <div class="ln lead" style="left:38px;top:922px;font-size:32px">If there is no one left to follow, then</div>
  <div class="ln lead" style="left:722px;top:940px;font-size:52px">lead<span style="font-size:22px">!</span></div>
  <div class="ln delight" style="left:38px;top:960px;font-size:26px"><span style="font-size:46px">Delight</span> your clients and colleagues</div>
  <div class="ln delight" style="left:38px;top:1006px;font-size:24px">by exceeding their <span style="font-size:34px">expectations</span>.</div>
  <div class="ln nurse" style="left:38px;top:1056px;font-size:58px">Nurse</div>
  <div class="ln nurse" style="left:222px;top:1050px;font-size:34px">with open hands,</div>
  <div class="ln nurse" style="left:222px;top:1088px;font-size:34px">hearts and minds.</div>

  <div class="brand-mark" aria-hidden="true"></div>
  <div class="brand-name">CalmPeak<br>For Nurses</div>

  <div class="partner-square" aria-hidden="true"></div>
  <div class="partner-name">Care Growth Partners</div>

  <div class="tagline">Live your <b>dream</b>.</div>
</main>
</body>
</html>
```